ORLA - Óptica Médica - web design and concept

Website concept - Create and develop our website design and structure. ORLA is an optical store chain, and we are looking to establish our web and digital concept. In attachment there are several pictures about our stores and our logo.

The website structure should be user friendly. Colors should be light and the design as simple and minimalist as possible. There are different variations of the logothat can be used, check the file.

The website will include optical collections and sun collections as an online store. Also, a medical menu should be considered in order for clients to schedule optometry appointments. There should also be a menu for client assistance where the clients can read about glass maintenance in our workshop.
Updates

Low design quality

Number of Pages Required

5+ page

Font styles to use
Serif
Sans Serif

Requirements
Must have
• Must be user-friendly and minimalist.
• Please USE PICTURES FROM THE BRANDS we sell: MERUN, BOSKA, PNW, KOLE, BAMPE
Nice to have
• Nice to inspire: ZEK glasses (see website https://ch.shopzek.com/en/)
• Nice to inspire: https://merun-eyewear.com/
• Nice to ispire: https://www.pnwglobe.com/en/
Should not have
• Hysteric colors and shapes

```html
<!DOCTYPE html>
<html lang="en">
<head>
<meta charset="utf-8">
<title>ORLA Óptica Médica – Medical Section</title>
<link href="https://fonts.googleapis.com/css2?family=Lato:wght@300;400;700&display=swap" rel="stylesheet">
<style>
:root{
  --gold:#e9b458;
  --ink:#1f1f1f;
  --muted:#555;
  --line:#c9c9c9;
  --band:#f3f4f6;
  --black:#000;
  --white:#fff;
}
*{box-sizing:border-box;margin:0;padding:0}
html,body{width:1200px;height:2844px;overflow:hidden;background:var(--white)}
body{position:relative;font-family:"Lato",sans-serif;color:var(--ink)}
.abs{position:absolute}

/* header */
.social{left:160px;top:16px;display:flex;gap:10px}
.social span{width:10px;height:10px;border-radius:50%;background:var(--ink)}
.brand{left:0;width:1200px;top:12px;text-align:center}
.brand-name{font-size:38px;font-weight:300;letter-spacing:4px;line-height:1}
.brand-sub{font-size:7px;letter-spacing:3px;color:var(--muted);margin-top:4px}
.topbar{top:14px;right:160px;display:flex;gap:34px;font-size:11px;align-items:center}
.topbar div{display:flex;gap:6px;align-items:center}
.nav{top:104px;left:0;width:1200px;display:flex;justify-content:center;gap:30px;font-size:11px;align-items:center}
.nav a{color:var(--ink);text-decoration:none}
.nav a.active{color:var(--gold)}
.nav .cta{background:var(--gold);padding:5px 7px;border:1px solid #c48f2f}

.page-title{top:205px;width:1200px;text-align:center;font-size:46px;font-weight:300}

/* intro */
.intro-text{left:160px;top:378px;width:418px}
.intro-text h2{font-size:24px;font-weight:300;white-space:nowrap;letter-spacing:-0.2px}
.rule{width:130px;height:5px;border-top:1px solid var(--gold);border-bottom:1px solid var(--gold);margin-top:14px}
.rule.center{margin:14px auto 0}
.intro-text p{font-size:10.5px;line-height:13.5px;margin-top:40px}
.btn{display:inline-block;background:var(--gold);font-size:13px;text-align:center;border:1px solid #d9a243}
.intro-text .btn{width:184px;height:52px;line-height:52px;margin-top:26px}
.intro-photo{left:600px;top:364px;width:441px;height:283px;background:linear-gradient(120deg,#e7e9ec,#c9cdd3 55%,#8e8f93)}

/* services */
.services{left:160px;top:732px;width:881px;display:flex;gap:17px}
.card{width:207px}
.card-photo{height:205px}
.card h3{font-size:23px;font-weight:300;margin-top:32px}
.card p{font-size:10px;line-height:14px;margin-top:14px}
.more{font-size:11px;margin-top:12px;display:flex;align-items:center;gap:6px}
.more svg{width:11px;height:11px}

/* appointment */
.form-title{top:1228px;width:1200px;text-align:center;font-size:25px;font-weight:300}
.label{font-size:11px}
.field{border:1px solid var(--line);background:var(--white)}
.submit{left:160px;top:1879px;width:181px;height:53px;line-height:53px}

/* features */
.feature{top:2010px;height:89px;border:1px solid var(--line);display:flex;align-items:center;justify-content:center;gap:10px}
.feature svg{width:30px;height:30px}
.feature b{display:block;font-size:17px;font-weight:300;color:var(--muted)}
.feature small{display:block;font-size:9px}

/* brands */
.brands{top:2137px;left:0;width:1200px;height:163px;background:var(--band);display:flex;align-items:center;justify-content:center;gap:78px}
.brands .logo{font-size:26px;font-weight:400;color:var(--ink);letter-spacing:1px}
.chev{top:2195px;width:28px;height:46px}

/* newsletter */
.news-title{top:2337px;width:1200px;text-align:center;font-size:25px;font-weight:300}
.news-input{left:303px;top:2412px;width:506px;height:68px;border:1px solid var(--line);border-right:none;font-size:11px;padding-left:30px;line-height:68px}
.news-btn{left:808px;top:2412px;width:91px;height:68px;background:var(--gold);display:flex;align-items:center;justify-content:center}

/* footer */
.footer{top:2518px;left:0;width:1200px;height:326px;background:var(--black);color:var(--white)}
.f-col{top:90px;font-size:10px;line-height:17px}
.f-col h4{color:var(--gold);font-size:12px;font-weight:700;margin-bottom:18px}
.f-col ul{list-style:none}
.f-col li::before{content:"•";margin-right:8px}
.f-brand{left:160px;top:55px;width:160px;font-size:10px;line-height:14px}
.f-brand .name{color:var(--gold);font-size:22px;font-weight:300;letter-spacing:3px;margin-bottom:14px}
.f-social{display:flex;gap:9px;margin-top:10px}
.f-social span{width:9px;height:9px;border-radius:50%;background:var(--gold)}
.f-rule{top:224px;left:160px;width:881px;border-top:1px solid #555}
.f-bottom{top:236px;font-size:11px}
</style>
</head>
<body>

<header>
  <div class="abs social" aria-label="Social links"><span></span><span></span><span></span><span></span><span></span></div>
  <div class="abs brand">
    <div class="brand-name">ORLA</div>
    <div class="brand-sub">ÓPTICA MÉDICA</div>
  </div>
  <div class="abs topbar">
    <div><svg width="10" height="11" viewBox="0 0 10 11"><rect x="1" y="4" width="8" height="7" fill="#1f1f1f"/><path d="M3 4V2.5a2 2 0 0 1 4 0V4" fill="none" stroke="#1f1f1f"/></svg>Your Cart ( 0 )</div>
    <div><svg width="11" height="11" viewBox="0 0 24 24"><path d="M6.6 10.8a15 15 0 0 0 6.6 6.6l2.2-2.2a1 1 0 0 1 1-.25 11 11 0 0 0 3.6.6 1 1 0 0 1 1 1V20a1 1 0 0 1-1 1A17 17 0 0 1 3 4a1 1 0 0 1 1-1h3.5a1 1 0 0 1 1 1 11 11 0 0 0 .6 3.6 1 1 0 0 1-.25 1z" fill="#1f1f1f"/></svg>+000-555-0142</div>
  </div>
  <nav class="abs nav">
    <a href="#">Home</a><a href="#">Online store</a><a href="#">Company history</a><a href="#" class="active">Medical section</a><a href="#">Store</a><a href="#">Contact Us</a><a href="#" class="cta">Make an Appoinment</a>
  </nav>
</header>

<h1 class="abs page-title">Medical Section</h1>

<section>
  <div class="abs intro-text">
    <h2>Diagnose &amp; Treatment of Eye Diseases</h2>
    <div class="rule"></div>
    <p>Lorem Ipsum is simply dummy text of the printing and typesetting industry. Lorem Ipsum has been the industry's standard dummy text ever since the 1500s, when an unknown printer took a galley of type and scrambled it to make a type specimen book. It has survived not only five centuries, but also the leap into electronic typesetting, remaining essentially unchanged. It was popularised in the 1960s with the release of transfer sheets containing Lorem Ipsum passages, and more recently with desktop publishing software including many versions of Lorem Ipsum.</p>
    <span class="btn">READ MORE</span>
  </div>
  <div class="abs intro-photo" role="img" aria-label="Photo of an optometrist examining a patient's eyes with a slit lamp"></div>
</section>

<section class="abs services">
  <article class="card">
    <div class="card-photo" role="img" aria-label="Close-up photo of an eye beside an eye chart" style="background:linear-gradient(135deg,#efeeec,#c8b8a6 60%,#8d6d4f)"></div>
    <h3>Eye Exam</h3>
    <p>Lorem Ipsum is simply dummy text of the printing and typesetting industry. Lorem Ipsum has been the industry's standard dummy text ever since the 1500s, when an unknown printer took a galley of type and scrambled it to make a type specimen book.</p>
    <div class="more">READ MORE... <svg viewBox="0 0 12 12"><circle cx="6" cy="6" r="5" fill="none" stroke="#1f1f1f"/><path d="M5 3.5 7.5 6 5 8.5" fill="none" stroke="#1f1f1f"/></svg></div>
  </article>
  <article class="card">
    <div class="card-photo" role="img" aria-label="Photo of black eyeglasses in front of an eye chart" style="background:linear-gradient(180deg,#f1f1f1,#dcdcdc 55%,#9a9a9a)"></div>
    <h3>Lense Exam</h3>
    <p>Lorem Ipsum is simply dummy text of the printing and typesetting industry. Lorem Ipsum has been the industry's standard dummy text ever since the 1500s, when an unknown printer took a galley of type and scrambled it to make a type specimen book.</p>
    <div class="more">READ MORE... <svg viewBox="0 0 12 12"><circle cx="6" cy="6" r="5" fill="none" stroke="#1f1f1f"/><path d="M5 3.5 7.5 6 5 8.5" fill="none" stroke="#1f1f1f"/></svg></div>
  </article>
  <article class="card">
    <div class="card-photo" role="img" aria-label="Photo of a doctor checking a child's eyes with a penlight" style="background:linear-gradient(120deg,#f4f4f4,#e3d6cc 50%,#b08d72)"></div>
    <h3>Pediatric Eye Care</h3>
    <p>Lorem Ipsum is simply dummy text of the printing and typesetting industry. Lorem Ipsum has been the industry's standard dummy text ever since the 1500s, when an unknown printer took a galley of type and scrambled it to make a type specimen book.</p>
    <div class="more">READ MORE... <svg viewBox="0 0 12 12"><circle cx="6" cy="6" r="5" fill="none" stroke="#1f1f1f"/><path d="M5 3.5 7.5 6 5 8.5" fill="none" stroke="#1f1f1f"/></svg></div>
  </article>
  <article class="card">
    <div class="card-photo" role="img" aria-label="Photo of a child covering one eye during a vision test" style="background:linear-gradient(120deg,#eceef0,#d9d2c6 55%,#b9a282)"></div>
    <h3>Vision Therapy</h3>
    <p>Lorem Ipsum is simply dummy text of the printing and typesetting industry. Lorem Ipsum has been the industry's standard dummy text ever since the 1500s, when an unknown printer took a galley of type and scrambled it to make a type specimen book.</p>
    <div class="more">READ MORE... <svg viewBox="0 0 12 12"><circle cx="6" cy="6" r="5" fill="none" stroke="#1f1f1f"/><path d="M5 3.5 7.5 6 5 8.5" fill="none" stroke="#1f1f1f"/></svg></div>
  </article>
</section>

<section class="appointment">
  <div class="abs form-title">Bool an Appoinment<div class="rule center"></div></div>
  <div class="abs label" style="left:160px;top:1300px">Full Name</div>
  <div class="abs field" style="left:160px;top:1327px;width:881px;height:61px"></div>
  <div class="abs label" style="left:160px;top:1403px">E-Mail Address</div>
  <div class="abs field" style="left:160px;top:1426px;width:429px;height:61px"></div>
  <div class="abs label" style="left:611px;top:1403px">Phone Number</div>
  <div class="abs field" style="left:611px;top:1426px;width:430px;height:61px"></div>
  <div class="abs label" style="left:160px;top:1504px">Date</div>
  <div class="abs field" style="left:160px;top:1528px;width:429px;height:61px"></div>
  <div class="abs label" style="left:611px;top:1504px">Time</div>
  <div class="abs field" style="left:611px;top:1528px;width:430px;height:61px"></div>
  <div class="abs label" style="left:160px;top:1605px">Massage</div>
  <div class="abs field" style="left:160px;top:1632px;width:881px;height:203px"></div>
  <span class="abs btn submit">SUBMIT</span>
</section>

<section>
  <div class="abs feature" style="left:167px;width:286px">
    <svg viewBox="0 0 30 30"><circle cx="15" cy="12" r="8" fill="none" stroke="#e9b458" stroke-width="1.5"/><path d="M11 22h8M12 26h6" stroke="#e9b458" stroke-width="1.5"/></svg>
    <div><b>Free Shipping</b><small>Lorem Ipsum is dummy text.</small></div>
  </div>
  <div class="abs feature" style="left:461px;width:284px">
    <svg viewBox="0 0 30 30"><circle cx="15" cy="15" r="12" fill="none" stroke="#e9b458" stroke-width="1.5"/><circle cx="15" cy="12" r="3.5" fill="none" stroke="#e9b458" stroke-width="1.5"/><path d="M9 22a6 6 0 0 1 12 0" fill="none" stroke="#e9b458" stroke-width="1.5"/></svg>
    <div><b>Premium Support</b><small>24/7 Customer service</small></div>
  </div>
  <div class="abs feature" style="left:755px;width:286px">
    <svg viewBox="0 0 30 30"><rect x="2" y="8" width="16" height="12" fill="none" stroke="#e9b458" stroke-width="1.5"/><path d="M18 12h6l4 4v4H18z" fill="none" stroke="#e9b458" stroke-width="1.5"/><circle cx="8" cy="22" r="2.5" fill="#fff" stroke="#e9b458" stroke-width="1.5"/><circle cx="23" cy="22" r="2.5" fill="#fff" stroke="#e9b458" stroke-width="1.5"/></svg>
    <div><b>Payment Method</b><small>Cash On Delivery</small></div>
  </div>
</section>

<section class="abs brands" aria-label="Partner brands">
  <span class="logo">Solvane</span>
  <span class="logo">Nerido</span>
  <span class="logo">Mira Lune</span>
  <span class="logo">Quillane</span>
  <span class="logo">Teskal</span>
</section>
<svg class="abs chev" style="left:78px" viewBox="0 0 28 46"><path d="M22 4 6 23l16 19" fill="none" stroke="#1f1f1f" stroke-width="2.5"/></svg>
<svg class="abs chev" style="left:1100px" viewBox="0 0 28 46"><path d="M6 4l16 19L6 42" fill="none" stroke="#e9b458" stroke-width="2.5"/></svg>

<section>
  <div class="abs news-title">Subscribe For Our Newsletter<div class="rule center"></div></div>
  <div class="abs news-input">E-Mail Address</div>
  <div class="abs news-btn"><svg width="36" height="30" viewBox="0 0 36 30"><path d="M2 3l32 12L2 27l5-12z M7 15h27" fill="none" stroke="#1f1f1f" stroke-width="2" stroke-linejoin="round"/></svg></div>
</section>

<footer class="abs footer">
  <div class="abs f-brand">
    <div class="name">ORLA</div>
    Lorem Ipsum is simply dummy text of the printing and typesetting industry.
    <div style="margin-top:8px">READ MORE....</div>
    <div class="f-social"><span></span><span></span><span></span><span></span><span></span></div>
  </div>
  <div class="abs f-col" style="left:424px"><h4>QUICK LINK</h4><ul><li>Women</li><li>Men</li><li>Youth</li><li>Collections</li><li>Contact Us</li></ul></div>
  <div class="abs f-col" style="left:637px"><h4>ACCOUNT</h4><ul><li>My Account</li><li>My Wishlist</li><li>Checkout</li><li>Create Account</li><li>Register</li></ul></div>
  <div class="abs f-col" style="left:860px"><h4>QUICK CONTACT</h4>
    <div>☎&nbsp; +000-555-0187</div>
    <div>✉&nbsp; info@orlaopticamedica.com</div>
    <div>●&nbsp; 14 Linden Row,<br>&nbsp;&nbsp;&nbsp;&nbsp;Brookhaven, NJ 00000</div>
  </div>
  <div class="abs f-rule"></div>
  <div class="abs f-bottom" style="left:164px">CopyRight ©2018 Orla Óptica Médica. All Right Reserve</div>
  <div class="abs f-bottom" style="left:822px">Privacy Policy - Terms &amp; Conditions</div>
</footer>

</body>
</html>
```